Letterhead, stationery and email signature for construction business

I need the letterhead, stationery and email signature designs for a construction business. I want them to have a corporate feel to them.

I've attached the logo for reference.

```html
<!DOCTYPE html>
<html lang="en">
<head>
<meta charset="utf-8">
<title>Harlow Build Stationery</title>
<link href="https://fonts.googleapis.com/css2?family=Lato:wght@400;700&family=Open+Sans:wght@400;700&display=swap" rel="stylesheet">
<style>
  :root{
    --brand-blue:#2f56a6;
    --ink:#1a1a1a;
    --header-black:#161616;
    --paper:#ffffff;
    --backdrop:#f4f4f4;
    --rule-grey:#d9d9de;
    --faint-panel:#eef0f8;
    --icon-blue:#2f6fc4;
  }
  html,body{margin:0;padding:0;overflow:hidden;}
  body{width:1200px;height:807px;background:var(--backdrop);position:relative;font-family:"Lato",sans-serif;color:var(--ink);}
  .sheet{position:absolute;background:var(--paper);box-sizing:border-box;}

  /* Letterhead */
  .letterhead{left:136px;top:97px;width:431px;height:610px;}
  .letterhead__band{position:absolute;left:0;top:0;width:431px;height:50px;background:var(--header-black);}
  .letterhead__stripe{position:absolute;left:0;top:50px;width:431px;height:5px;background:var(--brand-blue);}
  .brand-name{position:absolute;font-family:"Lato",sans-serif;font-weight:700;color:var(--brand-blue);letter-spacing:.5px;white-space:nowrap;}
  .letterhead .brand-name{left:21px;top:11px;font-size:23px;}
  .contact{position:absolute;font-size:8px;line-height:9.5px;color:#333;}
  .contact p{margin:0;}
  .contact .gap{height:9px;}
  .contact-row{display:flex;align-items:center;gap:3px;}
  .contact-row svg{width:7px;height:7px;flex:none;}
  .letterhead .contact{left:309px;top:61px;}
  .letter-body{position:absolute;left:21px;top:160px;width:389px;font-size:9px;line-height:9.6px;}
  .letter-body p{margin:0 0 10px;}
  .letter-body .greeting{font-size:11px;font-weight:700;margin:12px 0 11px;}
  .letter-body .para{text-align:justify;margin-bottom:9.5px;}
  .letter-body .closing{margin-top:20px;}
  .signature{position:absolute;left:21px;top:505px;width:92px;height:24px;background:#e6e6e6;}

  /* Email signature */
  .email-signature{left:620px;top:69px;width:475px;height:147px;font-family:"Open Sans",sans-serif;}
  .portrait{position:absolute;left:21px;top:24px;width:96px;height:96px;border-radius:50%;border:1.5px solid var(--brand-blue);background:linear-gradient(160deg,#d9d4cc,#c9b69a 55%,#e3e1dd);box-sizing:border-box;}
  .person{position:absolute;left:166px;top:19px;}
  .person__name{margin:0;font-size:12.5px;font-weight:700;color:var(--brand-blue);line-height:14px;}
  .person__title{margin:0;font-size:8px;color:#333;line-height:10px;}
  .rule{width:37px;height:1px;background:var(--brand-blue);margin:6px 0 5px;}
  .email-signature .contact{position:static;font-family:"Open Sans",sans-serif;font-size:8px;line-height:11px;}
  .email-signature .brand-name{left:287px;top:30px;font-size:21px;}
  .social{position:absolute;left:402px;top:114px;display:flex;gap:3px;}
  .social span{width:11px;height:11px;border-radius:50%;background:var(--icon-blue);}

  /* Envelope back */
  .envelope-back{left:620px;top:269px;width:440px;height:194px;}
  .envelope-back svg{position:absolute;left:0;top:0;}
  .envelope-back .brand-name{left:0;width:440px;text-align:center;top:20px;font-size:12px;}

  /* Envelope front */
  .envelope-front{left:620px;top:516px;width:440px;height:191px;overflow:hidden;}
  .envelope-front .brand-name{left:13px;top:22px;font-size:19px;}
  .envelope-front .contact{left:13px;top:154px;font-family:"Open Sans",sans-serif;font-size:8px;line-height:11px;}
  .accent-panel{position:absolute;left:280px;top:0;width:160px;height:191px;background:linear-gradient(120deg,#f1f1f3,var(--faint-panel));}
</style>
</head>
<body>

<section class="sheet letterhead">
  <div class="letterhead__band" role="img" aria-label="Dark header band with sweeping blue wave decoration"></div>
  <div class="letterhead__stripe"></div>
  <div class="brand-name">HARLOW BUILD</div>
  <div class="contact">
    <p>Your address, City</p>
    <p>State, Zip 1234</p>
    <div class="gap"></div>
    <div class="contact-row"><svg viewBox="0 0 10 10"><path d="M1 4C1 2 3 1 5 1S9 2 9 4L7 4 6.5 3H3.5L3 4ZM2 5H8V9H2Z" fill="var(--icon-blue)"/></svg>123 456 789</div>
    <div class="contact-row"><svg viewBox="0 0 10 10"><rect x="1" y="2" width="8" height="6" fill="var(--icon-blue)"/><path d="M1 2L5 5.5 9 2" stroke="#fff" fill="none"/></svg>info@harlowbuild.com</div>
    <div class="contact-row"><svg viewBox="0 0 10 10"><circle cx="5" cy="5" r="4" fill="var(--icon-blue)"/><path d="M1 5H9M5 1V9" stroke="#fff" stroke-width=".7"/></svg>www.harlowbuild.com</div>
  </div>
  <div class="letter-body">
    <p>January-03-2020</p>
    <p>Mr, Paul Reyes<br>President</p>
    <p>Norfield Group<br>123 Street Name, Suite# 10<br>City, State, 120023</p>
    <p class="greeting">Dear Mr, Paul</p>
    <p class="para">Lorem ipsum dolor sit amet, consectetur adipiscing elit, sed do eiusmod tempor incididunt ut labore et dolore magna aliqua. Ut enim ad minim veniam, quis nostrud exercitation ullamco laboris nisi ut aliquip ex ea commodo consequat. Duis aute irure dolor in reprehenderit in voluptate velit esse cillum dolore eu fugiat nulla pariatur.</p>
    <p class="para">Lorem ipsum dolor sit amet, consectetur adipiscing elit, sed do eiusmod tempor incididunt ut labore et dolore magna aliqua. Ut enim ad minim veniam, quis nostrud exercitation ullamco laboris nisi ut aliquip ex ea commodo consequat. Duis aute irure dolor in reprehenderit in voluptate velit esse cillum dolore eu fugiat nulla pariatur.</p>
    <p class="para">Lorem ipsum dolor sit amet, consectetur adipiscing elit, sed do eiusmod tempor incididunt ut labore et dolore magna aliqua. Ut enim ad minim veniam, quis nostrud exercitation ullamco laboris nisi ut aliquip ex ea commodo consequat.</p>
    <p class="para">Excepteur sint occaecat cupidatat non proident, sunt in culpa qui officia deserunt mollit anim id est laborum. re et dolore magnam aliquam quaerat voluptatem.</p>
    <p class="closing">Regards</p>
  </div>
  <div class="signature" role="img" aria-label="Handwritten signature of Lena Brooks"></div>
</section>

<section class="sheet email-signature">
  <div class="portrait" role="img" aria-label="Portrait photo of Owen Carter"></div>
  <div class="person">
    <p class="person__name">OWEN CARTER</p>
    <p class="person__title">Managing Director</p>
    <div class="rule"></div>
    <div class="contact">
      <p>Your address, City</p>
      <p>State, Zip 1234</p>
    </div>
    <div class="rule"></div>
    <div class="contact">
      <div class="contact-row"><svg viewBox="0 0 10 10"><path d="M1 4C1 2 3 1 5 1S9 2 9 4L7 4 6.5 3H3.5L3 4ZM2 5H8V9H2Z" fill="var(--icon-blue)"/></svg>123-456-789</div>
      <div class="contact-row"><svg viewBox="0 0 10 10"><rect x="1" y="2" width="8" height="6" fill="var(--icon-blue)"/><path d="M1 2L5 5.5 9 2" stroke="#fff" fill="none"/></svg>owen@harlowbuild.com</div>
      <div class="contact-row"><svg viewBox="0 0 10 10"><circle cx="5" cy="5" r="4" fill="var(--icon-blue)"/><path d="M1 5H9M5 1V9" stroke="#fff" stroke-width=".7"/></svg>www.harlowbuild.com</div>
    </div>
  </div>
  <div class="brand-name">HARLOW BUILD</div>
  <div class="social" aria-label="Social links"><span></span><span></span><span></span><span></span></div>
</section>

<section class="sheet envelope-back">
  <svg width="440" height="194" viewBox="0 0 440 194" aria-hidden="true">
    <path d="M0 0C6 18 18 36 34 39L220 60 406 39C422 36 434 18 440 0" fill="none" stroke="var(--rule-grey)" stroke-width="1.5"/>
  </svg>
  <div class="brand-name">HARLOW BUILD</div>
</section>

<section class="sheet envelope-front">
  <div class="accent-panel"></div>
  <div class="brand-name">HARLOW BUILD</div>
  <div class="contact">
    <p>Your address, City</p>
    <p>State, Zip 1234</p>
  </div>
</section>

</body>
</html>
```